Stationery Design Project

We need a stationery design for our Norwegian trucking company. We have existed for about 15 years and our 12 drivers uses relatively new vehicles to transport goods around in northern Norway. Long distance routes with fresh fish og food transport is our main operations.

We have already made alogo that's printed on our trucks. The logo and a picture of our trucks is attached. I think the logo i crappy, but since its already in use, changing it is not an option in this round. Still using a better colour scheme in the overall stationery and more interesting fonts is possible (altso in the logo).

Company details:
Name: Kjelvraket AS
Organisation nr 873 615 309
Post adress: 8642 Raudvik

I like minimalism and simplicity. I am avalibly for questions in normal GMT working hours either here or on mail: ivar@fjordlast.no

Reason: Hi. Im extending the deadline because I needed some time to find a vector file of our logo. Sorry for the inconvenience

Hi, and thanks for all your interest in the project. Some updates:

-          I have decided to commit to using one of the designs. Some designer will get the payment.

-          I have extended the deadline with 24 hours since I needed some time to find our firms vector logo (a slow Swedish man was holding me up)

-          We will not choose a design before the deadline. No need to rush.

-          We have received a lot of great design and think there is a need to specified the product we want to make:

o   Business Card for all our employers. I just need the design and will duplicate with the correct numbers and name myself. The information on should be: Logo, employer’s name, Phone number, email, website, Postal number and address. Use this as a template: logo, Leif Brattvoll, 47382066, Leif@fjordlast.no,, fjordlast.no, 8642 Raudvik. The order and placement of the information is your creative decision.

o   Stickers to put on the goods we travel. On the sticker the should be the following information: Logo, phone number, Tekst and link: Fraktæ av Kjelvraket. Ke du syns? Fjordlast.no/tilbakemelding (this means: Handled by Kjelvraket. What do you think Fjordlast.no/feedback -à the link will be a feedback form). The placement the information and size is your creative decision with some stings: we have been thinking of using Drukko for printing and see that a size about 6x6 cm, 8x5 or something like that. (with 3000 copies our budget is 200 punds). Any suggestions of other suppliers are welcome. Drukko price calculator http://www.drukkolabelhouse.co.uk/digital-litho-printing/printing-labels-tags/stickers/

o   Letterhead with logo, address, phone number and organizational number.

o   Envelopes with logo,address, phone number and organizational number.

Have a nice day.

 

 

• Using the blue colour in the logo and using a similar graphic approch.

```html
<!DOCTYPE html>
<html lang="no">
<head>
<meta charset="UTF-8">
<title>Kjelvraket AS – visittkort</title>
<link rel="stylesheet" href="https://fonts.googleapis.com/css2?family=Open+Sans:wght@400;600;700&display=swap">
<style>
  :root {
    --backdrop: #1c1c22;
    --brand-blue: #1d4fa6;
    --card-white: #ffffff;
    --card-black: #1e1c1d;
    --ink: #3a3a3a;
    --band-black: #151515;
    --line-grey: #9a9a9a;
    --url-grey: #6e6e6e;
    --url-light: #bdbdbd;
  }
  * { margin: 0; padding: 0; box-sizing: border-box; }
  html, body { width: 1200px; height: 246px; overflow: hidden; }
  body {
    background: var(--backdrop);
    font-family: "Open Sans", Arial, sans-serif;
    position: relative;
  }
  .card {
    position: absolute;
    top: 14px;
    width: 274px;
    height: 218px;
    border-radius: 12px;
    overflow: hidden;
  }
  .card--front { left: 17px; background: var(--card-white); }
  .card--back-light { left: 463px; background: var(--card-white); }
  .card--back-dark { left: 909px; background: var(--card-black); }

  .brand-name {
    position: absolute;
    font-weight: 700;
    color: var(--brand-blue);
    letter-spacing: -0.5px;
    white-space: nowrap;
    display: flex;
    align-items: center;
    gap: 8px;
  }
  .brand-name::before {
    content: "";
    width: 14px; height: 14px;
    border-radius: 50%;
    background: var(--brand-blue);
  }
  .card--front .brand-name { left: 26px; top: 40px; font-size: 24px; }
  .card--back-light .brand-name,
  .card--back-dark .brand-name {
    left: 50%; top: 66px; transform: translateX(-50%); font-size: 28px;
  }

  .contact {
    position: absolute;
    left: 22px;
    top: 96px;
    color: var(--ink);
    font-size: 8px;
    line-height: 15px;
  }
  .contact .person { font-size: 10px; line-height: 16px; }

  .swoosh { position: absolute; left: 0; top: 0; width: 274px; height: 218px; }
  .swoosh .band-blue { fill: var(--brand-blue); }
  .swoosh .band-black { fill: var(--band-black); }
  .swoosh .rule { fill: none; stroke: var(--line-grey); stroke-width: 1; }

  .legal {
    position: absolute;
    right: 14px;
    bottom: 12px;
    text-align: right;
    color: var(--card-white);
    font-size: 8px;
    line-height: 12px;
  }

  .web {
    position: absolute;
    left: 0; right: 0;
    bottom: 18px;
    text-align: center;
    font-size: 7px;
    letter-spacing: 2.6px;
  }
  .card--back-light .web { color: var(--url-grey); }
  .card--back-dark .web { color: var(--url-light); }
</style>
</head>
<body>
  <section class="card card--front">
    <svg class="swoosh" viewBox="0 0 274 218" aria-hidden="true">
      <path class="rule" d="M0,150 Q150,160 274,94"/>
      <path class="band-black" d="M0,157 Q150,168 274,102 L274,112 Q150,177 0,165 Z"/>
      <path class="band-blue" d="M0,171 Q150,182 274,118 L274,218 L0,218 Z"/>
    </svg>
    <div class="brand-name">Kjelvraket</div>
    <div class="contact">
      <p class="person">Leif Brattvoll</p>
      <p>47382066</p>
      <p>Leif@fjordlast.no</p>
      <p>www.fjordlast.no</p>
    </div>
    <div class="legal">
      <p>8642 Raudvik.</p>
      <p>Organisation nr 873 615 309</p>
    </div>
  </section>

  <section class="card card--back-light">
    <div class="brand-name">Kjelvraket</div>
    <p class="web">www.fjordlast.no</p>
  </section>

  <section class="card card--back-dark">
    <div class="brand-name">Kjelvraket</div>
    <p class="web">www.fjordlast.no</p>
  </section>
</body>
</html>
```